Business Cards for new orthopaedic surgery practice

My husband and I are starting our own orthopaedic surgery practice. We are looking for a business card that is uniform, but one will have my name/title and the other will have his. You can just create one design with my name on it for now. But when I choose your design as the winning design I will ask that you add another copy with his name/title.

We are looking for classy, simple, elite all in one. We like dark blues/a little gold/yellow. Something that goes with our logo. We want our logo incorporated. Here is all the info you need:
Business name: RV Bone & Vitality Center
Location: 38517 North Willowmere Ave
Maple Harbor, FL 33990
Phone: 954-218-4063
Fax: 954-582-7341
Email: info@myrvbonecare.example

Names: Lydia Vance, M.D.
Board Certified Hand and Upper Extremity Surgeon

Ebo Dansu, M.D.
Board Certified Hip & Knee Replacement/General Orthopaedic Surgeon

Can decide what you want to put on the back. Maybe a slogan:
Rooted in Care. Focused on You

I am just going to upload our logo. The only thing is if we select you as the winning design, the location, and phone numbers may change. We will need your help to update that once fully solidified.

Industry/Entity Type

Medical

Contact Information for Business Card

Colors
0054AA
0677BA
7BADD7
CADEEF
E8F1F8
0094D4
00A9DD
6FCCEA
C7EBF8
E9F6FB

Requirements
Must have
• class, appeal,
Should not have
• We want to air on the side of masculine if we are looking at masculine vs. feminine feel. But we still want it classy, sophisticated, and something we will love

```html
<!DOCTYPE html>
<html lang="en">
<head>
<meta charset="utf-8">
<title>RV Bone &amp; Vitality Center – Business Card</title>
<link rel="stylesheet" href="https://fonts.googleapis.com/css2?family=Tinos:wght@400;700&display=swap">
<style>
  :root {
    --page-bg: #6f6f6f;
    --navy-light: #16274f;
    --navy-dark: #03022a;
    --navy-text: #13234d;
    --gold: #c9a35a;
    --ink: #3a3a3a;
    --paper: #ffffff;
    --watermark-light: #ececec;
    --watermark-dark: #1c2d58;
  }
  * { margin: 0; padding: 0; box-sizing: border-box; }
  html, body { width: 1200px; height: 840px; overflow: hidden; }
  body {
    background: var(--page-bg);
    font-family: "Tinos", "Times New Roman", serif;
    position: relative;
  }
  .card {
    position: absolute;
    width: 535px;
    height: 306px;
    overflow: hidden;
    box-shadow: 0 10px 24px rgba(0,0,0,0.28);
  }
  /* Back of card */
  .card-back {
    left: 185px; top: 92px;
    border-radius: 30px 0 30px 0;
    background: linear-gradient(90deg, var(--navy-light) 0%, #0a1640 45%, var(--navy-dark) 100%);
  }
  .card-back .mark-watermark {
    position: absolute;
    left: 26px; top: 110px;
    width: 150px;
    font-size: 26px;
    font-weight: 700;
    line-height: 1.15;
    color: var(--watermark-dark);
  }
  .card-back .slogan {
    position: absolute;
    left: 177px; top: 196px;
    font-size: 22px;
    color: var(--gold);
    white-space: nowrap;
  }
  /* Front of card */
  .card-front {
    left: 489px; top: 420px;
    border-radius: 0 30px 0 30px;
    background: var(--paper);
  }
  .card-front .mark-watermark {
    position: absolute;
    left: 20px; top: 258px;
    font-size: 20px;
    font-weight: 700;
    line-height: 1.15;
    color: var(--watermark-light);
    white-space: nowrap;
  }
  .contact {
    position: absolute;
    left: 20px; top: 18px;
    color: var(--ink);
    font-size: 15px;
    line-height: 1.25;
  }
  .contact .name {
    font-size: 17px;
    font-weight: 700;
    color: var(--navy-text);
  }
  .contact .title { margin-top: 1px; }
  .contact .address { margin-top: 17px; }
  .contact .lines { margin-top: 13px; list-style: none; }
  .contact .lines li {
    display: flex; align-items: center; gap: 6px;
    height: 23px;
  }
  .contact .lines svg { width: 13px; height: 13px; fill: var(--navy-text); flex: none; }
  .brand {
    position: absolute;
    left: 370px; top: 150px;
    width: 140px; height: 110px;
    display: flex; align-items: center; justify-content: center;
    text-align: center;
    font-size: 19px;
    font-weight: 700;
    line-height: 1.2;
    color: var(--navy-text);
  }
</style>
</head>
<body>
  <section class="card card-back" aria-label="Business card back">
    <div class="mark-watermark">RV Bone &amp; Vitality Center</div>
    <p class="slogan">Rooted in Care. Focused on You</p>
  </section>

  <section class="card card-front" aria-label="Business card front">
    <div class="mark-watermark">RV Bone &amp; Vitality Center</div>
    <div class="contact">
      <p class="name">Lydia Vance, M.D.</p>
      <p class="title">Board Certified Hand and Upper Extremity Surgeon</p>
      <p class="address">38517 North Willowmere Ave<br>Maple Harbor, FL 33990</p>
      <ul class="lines">
        <li>
          <svg viewBox="0 0 16 16" aria-hidden="true"><path d="M3.5 1.2l2.3 2.6c.4.4.3 1-.1 1.4L4.6 6.3c.8 1.9 2.6 3.8 4.9 5l1.1-1.1c.4-.4 1-.4 1.4-.1l2.6 2.1c.4.4.5 1 .1 1.4l-1.3 1.3c-.7.7-1.8.9-2.7.5C6.2 13.8 2.5 10 1 5.5.7 4.6.9 3.6 1.6 2.9L2.1 2.4c.4-.5 1-.6 1.4-1.2z"/></svg>
          <span>954-218-4063</span>
        </li>
        <li>
          <svg viewBox="0 0 16 16" aria-hidden="true"><path d="M4 1h6l2 2v3H4zM1.5 6.5h13c.6 0 1 .4 1 1V12h-3v3h-9v-3h-3V7.5c0-.6.4-1 1-1zM5 10v4h6v-4zM6 11h4v.8H6zm0 1.4h4v.8H6z"/></svg>
          <span>954-582-7341</span>
        </li>
        <li>
          <svg viewBox="0 0 16 16" aria-hidden="true"><path d="M1 3h14v10H1zM2.2 4.2v.4L8 8.8l5.8-4.2v-.4zm0 1.9v5.7l3.7-3zm11.6 0l-3.7 2.7 3.7 3zM7 9.6l-4.5 2.2h11L9 9.6 8 10.3z"/></svg>
          <span>info@myrvbonecare.example</span>
        </li>
      </ul>
    </div>
    <div class="brand">RV Bone &amp; Vitality Center</div>
  </section>
</body>
</html>
```